Maple Roster Business Card for recruitment company

We are looking for a Business Card Design that incorporates our personal details and our busines name and logo. We are a specialized search consultancy that recruit Property and Construction professionals.
We would like a business card that stands out and is appealing to the Construction and Property industry as well.

Target Market(s)

people in the construction and property industry

Contact Information for Business Card

Business Name and logo

Font styles to use
Serif

Colors
0094D4
00A9DD
6FCCEA
C7EBF8
E9F6FB

Requirements
Must have
• Business name and logo as well as contact details
Should not have
• No photos of us please

```html
<!DOCTYPE html>
<html lang="en">
<head>
<meta charset="utf-8">
<title>Maple Roster – Business Card</title>
<link href="https://fonts.googleapis.com/css2?family=Lora:wght@400;500;600&display=swap" rel="stylesheet">
<style>
  :root {
    --backdrop: #d3d3d3;
    --card-white: #ffffff;
    --brand-blue: #0094d4;
    --brand-sky: #00a9dd;
    --brand-light: #6fccea;
    --brand-pale: #c7ebf8;
    --brand-mist: #e9f6fb;
    --ink: #2b3a42;
    --on-blue: #ffffff;
  }
  * { margin: 0; padding: 0; box-sizing: border-box; }
  html, body { width: 900px; height: 1200px; overflow: hidden; }
  body {
    background: var(--backdrop);
    font-family: "Lora", Georgia, serif;
    position: relative;
  }
  .card {
    position: absolute;
    left: 79px;
    width: 743px;
    height: 441px;
  }
  .card--front { top: 131px; background: var(--card-white); }
  .card--back { top: 638px; height: 440px; background: var(--brand-blue); }

  .brand {
    position: absolute;
    left: 0; right: 0;
    display: flex;
    align-items: center;
    justify-content: center;
    gap: 18px;
  }
  .card--front .brand { top: 108px; }
  .card--back .brand { top: 190px; }
  .brand__mark {
    width: 50px;
    height: 50px;
    border-radius: 50%;
    flex: none;
  }
  .card--front .brand__mark { background: var(--brand-sky); }
  .card--back .brand__mark { background: var(--brand-pale); }
  .brand__name {
    font-weight: 500;
    font-size: 56px;
    letter-spacing: 3px;
    line-height: 1;
    text-transform: uppercase;
  }
  .card--front .brand__name { color: var(--brand-blue); }
  .card--back .brand__name { color: var(--on-blue); }

  .person {
    position: absolute;
    right: 429px;
    top: 242px;
    text-align: right;
  }
  .person__name {
    font-size: 25px;
    font-weight: 600;
    color: var(--brand-blue);
    line-height: 1.1;
  }
  .person__role {
    font-size: 16px;
    font-weight: 400;
    color: var(--ink);
    margin-top: 4px;
  }
  .divider {
    position: absolute;
    left: 365px;
    top: 240px;
    width: 2px;
    height: 66px;
    background: var(--brand-light);
  }
  .contacts {
    position: absolute;
    left: 410px;
    top: 237px;
    list-style: none;
  }
  .contacts li {
    display: flex;
    align-items: center;
    height: 24.5px;
    font-size: 16px;
    color: var(--ink);
  }
  .contacts svg { width: 14px; height: 14px; margin-right: 15px; fill: var(--brand-blue); flex: none; }
  .address-band {
    position: absolute;
    left: 0; right: 0;
    top: 355px;
    height: 40px;
    background: var(--brand-blue);
    color: var(--on-blue);
    font-size: 16px;
    display: flex;
    align-items: center;
    justify-content: center;
  }
  .footer-strip {
    position: absolute;
    left: 0; right: 0;
    top: 395px;
    bottom: 0;
    background: var(--brand-mist);
  }
</style>
</head>
<body>
  <section class="card card--front">
    <div class="brand">
      <span class="brand__mark" aria-hidden="true"></span>
      <span class="brand__name">Maple Roster</span>
    </div>
    <div class="person">
      <div class="person__name">Dana Holt</div>
      <div class="person__role">Owner/ Designer</div>
    </div>
    <div class="divider"></div>
    <ul class="contacts">
      <li>
        <svg viewBox="0 0 16 16" aria-hidden="true"><path d="M2 5c0-2 2-3 6-3s6 1 6 3v1h-3V5H5v1H2z M4 7h8l2 6H2z"/></svg>
        (555) 014-2287
      </li>
      <li>
        <svg viewBox="0 0 16 16" aria-hidden="true"><path d="M1 3h14v1L8 8.5 1 4z M1 5.5l7 4.5 7-4.5V13H1z"/></svg>
        info@mapleroster.com
      </li>
      <li>
        <svg viewBox="0 0 16 16" aria-hidden="true"><circle cx="8" cy="8" r="7"/><path d="M5 4c2 1 1 3 3 3s1 3 0 5c-2-1-3-3-3-5z M10 3c1 1 3 2 3 4-2 0-3-2-3-4z" fill="#ffffff"/></svg>
        www.mapleroster.com
      </li>
    </ul>
    <div class="address-band">208 Harbor Lane, Cedar Point, CA 90000</div>
    <div class="footer-strip"></div>
  </section>

  <section class="card card--back">
    <div class="brand">
      <span class="brand__mark" aria-hidden="true"></span>
      <span class="brand__name">Maple Roster</span>
    </div>
  </section>
</body>
</html>
```